Corporate-Design für Steuerberatungsgesellschaft
Zielgruppe
Wir sind eine Steuerberatungsgesellschaft mit 10 Mitarbeitern im Norden von Deutschland, kurz vor der Ostseeküste. Unser Unternehmen besteht seit 30 Jahren. Wir betreuen vor allem Mandanten in kleinen und mittleren Unternehmen: von der Arztpraxis bis zum Bauunternehmen. Demnächst werden wir neue Räume beziehen. Diese sollen großzügiger und moderner werden, teilweise mit Glaswänden.
Aufgabenstellung
Unser bisheriges Farbkonzept war von bordeaux und creme geprägt (www.kanzlei-mervato.de). Das muss aber nicht weiter bestehen. Das bisherige Logo finden wir inhaltlich recht treffend, aber es sollte moderner gestaltet werden. Der Schriftzug des Kanzleinamens soll an der Fassade in silbernen Buchstaben angebracht werden.

```html
<!DOCTYPE html>
<html lang="de">
<head>
<meta charset="utf-8">
<title>KVR Kestow – Visitenkarten</title>
<link rel="stylesheet" href="https://fonts.googleapis.com/css2?family=Noto+Serif:wght@400;700&display=swap">
<style>
  :root {
    --bg: #c9c9cc;
    --card-grey: #6d6d6e;
    --card-white: #ffffff;
    --brand-red: #9b1b2a;
    --text-grey: #5a5a5c;
    --text-white: #ffffff;
    --soft-white: #e4e4e4;
  }
  * { margin: 0; padding: 0; box-sizing: border-box; }
  html, body { width: 1200px; height: 852px; overflow: hidden; }
  body {
    background: var(--bg);
    font-family: "Noto Serif", Georgia, serif;
    position: relative;
  }
  .card {
    position: absolute;
    top: 258px;
    width: 520px;
    height: 336px;
    overflow: hidden;
    box-shadow: 0 6px 18px rgba(0,0,0,0.18);
  }
  /* Front side */
  .card--front { left: 50px; background: var(--card-grey); color: var(--text-white); }
  .brand {
    position: absolute;
    left: 60px;
    top: 110px;
    display: flex;
    align-items: center;
    gap: 16px;
  }
  .brand__square {
    width: 42px; height: 42px;
    background: var(--brand-red);
  }
  .brand__name {
    font-size: 42px;
    font-weight: 400;
    letter-spacing: 1px;
    line-height: 1;
    color: var(--text-white);
  }
  .brand__line {
    font-size: 12px;
    letter-spacing: 9px;
    margin-top: 8px;
    color: var(--soft-white);
  }
  .services {
    position: absolute;
    left: 36px;
    bottom: 40px;
    font-size: 11px;
    line-height: 1.55;
    color: var(--soft-white);
  }
  .rule {
    position: absolute;
    height: 4px;
    background: var(--brand-red);
  }
  .card--front .rule { left: 0; right: 0; bottom: 22px; }

  /* Back side */
  .card--back { left: 630px; background: var(--card-white); color: var(--text-grey); }
  .person {
    position: absolute;
    left: 36px;
    top: 40px;
  }
  .person__degree { font-size: 12px; }
  .person__name {
    font-size: 22px;
    font-weight: 700;
    color: var(--brand-red);
    margin: 2px 0 3px;
  }
  .person__role { font-size: 12px; }
  .office {
    position: absolute;
    left: 300px;
    top: 130px;
    font-size: 11px;
    line-height: 1.55;
  }
  .office__firm { font-weight: 700; }
  .office__firm .accent { color: var(--brand-red); }
  .contact { list-style: none; margin-top: 12px; }
  .contact li { display: flex; align-items: center; gap: 7px; }
  .contact svg { width: 11px; height: 11px; flex: none; }
  .card--back .rule { left: 300px; right: 0; bottom: 22px; }
</style>
</head>
<body>
  <section class="card card--front" aria-label="Vorderseite">
    <div class="brand">
      <div class="brand__square"></div>
      <div>
        <div class="brand__name">KVR Kestow</div>
        <div class="brand__line">STEUERBERATUNG</div>
      </div>
    </div>
    <p class="services">Steuerberatung / Finanz- und Lohnbuchhaltung<br>Betriebswirtschaftliche Beratung</p>
    <div class="rule"></div>
  </section>

  <section class="card card--back" aria-label="Rückseite">
    <div class="person">
      <p class="person__degree">Diplom-Kaufmann</p>
      <p class="person__name">Jonas Wendt - Albrecht</p>
      <p class="person__role">Geschäftsführer / Steuerberater</p>
    </div>
    <div class="office">
      <p class="office__firm"><span class="accent">KVR</span> Kestow</p>
      <p class="office__firm">Steuerberatungsgesellschaft mbH</p>
      <p>Lindenhofweg 4</p>
      <p>D - 17402 Kestow</p>
      <ul class="contact">
        <li><svg viewBox="0 0 12 12"><circle cx="6" cy="6" r="6" fill="#9b1b2a"/><path d="M4 3.2l1.2 1.6-.6.8c.4.9 1 1.5 1.9 1.9l.8-.6L8.9 8l-.7.9C6 8.7 3.4 6.1 3.1 3.9z" fill="#fff"/></svg>+49 (0) 38812 / 47 20 - 0</li>
        <li><svg viewBox="0 0 12 12"><circle cx="6" cy="6" r="6" fill="#9b1b2a"/><rect x="3.3" y="4.5" width="5.4" height="3.6" fill="#fff"/><rect x="4.2" y="3" width="3.6" height="1.5" fill="#fff"/></svg>+49 (0) 38812 / 47 20 - 49</li>
        <li><svg viewBox="0 0 12 12"><circle cx="6" cy="6" r="6" fill="#9b1b2a"/><rect x="3" y="4" width="6" height="4.2" fill="#fff"/><path d="M3 4l3 2.3L9 4" stroke="#9b1b2a" stroke-width=".7" fill="none"/></svg>kestow@kanzlei-mervato.de</li>
        <li><svg viewBox="0 0 12 12"><circle cx="6" cy="6" r="6" fill="#9b1b2a"/><circle cx="6" cy="6" r="3" fill="none" stroke="#fff" stroke-width=".8"/><path d="M3 6h6M6 3v6" stroke="#fff" stroke-width=".6"/></svg>www.kanzlei-mervato.de</li>
      </ul>
    </div>
    <div class="rule"></div>
  </section>
</body>
</html>
```